Company or website name
- Velmira, LLC
- Velmira, LLC
- Describe your company and organization and target audience
- Velmira, LLC is a research, science and technology based manufacturing company that formulates, develops, manufactures and packages a full complement of personal care products for domestic and international concerns. We private label and contract package personal care products, cosmetics, bath salts and powders and home fragrance products. Velmira is conveniently located in Southern California adjacent to major transportation hubs and international airports. We utilize earth friendly, green manufacturing processes, maximize the use of renewable resource raw materials and minimize the use of non-renewable and petrochemical based raw materials. We provide formulation and product development services with low minimum order quantities and short lead times. Velmira is the intersection between nature, science, beauty and innovation. We are a B-2-B company.
- The design should have the following
- We're looking for an ad design that can be used for both banner and column use online and in print. We manufacture bath and body products such as bath salts, body washes, body powders, bath oils and bubble baths, hair care products such as shampoos, conditioners and styling aids, skin care products such as anti-aging creams, cleansers, masks, toners and serums, color cosmetics such as eyeliners, mascaras, foundations and mineral make-up powders, manicure/pedicure products such as cuticle oils, sugar and salt scrubs and foot soaks/softeners and spa products such as seaweed wraps, cellulite creams, body masks, massage oils and candles. Our strengths are natural and organic product formulation, low minimums, competitive prices, complete research &development services new and innovative ingredients and fast turnaround times. Examples can be found at the following sites: http://www.glintor.com/ http://www.grovewellboard.org/ http://www.tessaloomjournal.com/ http://nerwast.org/images/downloads/bulletins/2009-10-bulletin.pdf http://www.pantrykestrelworks.com/

```html
<!DOCTYPE html>
<html lang="en">
<head>
<meta charset="utf-8">
<title>Velmira — Ad Set</title>
<link href="https://fonts.googleapis.com/css2?family=Crimson+Text:wght@400;600&display=swap" rel="stylesheet">
<style>
  :root{
    --red:#c8202f;
    --ink:#222;
    --paper:#fff;
    --rule:#9a9a9a;
    --logo-ink:#b5562a;
    --bg-top:#1a0f33;
    --bg-mid:#0b0b12;
    --bg-low:#173b1c;
  }
  html,body{margin:0;padding:0;overflow:hidden}
  body{width:1200px;height:1043px;position:relative;font-family:"Crimson Text",Georgia,serif;color:var(--ink);
    background:
      radial-gradient(ellipse 700px 260px at 250px 90px, #3a1f6e 0%, transparent 70%),
      radial-gradient(ellipse 900px 300px at 100px 560px, #3f6a43 0%, transparent 70%),
      linear-gradient(180deg,var(--bg-top) 0%,var(--bg-mid) 40%,var(--bg-low) 62%,#06140a 100%);}
  .ad{position:absolute;background:var(--paper);display:flex;flex-direction:column;overflow:hidden}
  .ad__photo{position:relative;flex:none;
    background:radial-gradient(circle at 42% 45%, #b8766a 0%, #8a5a55 18%, #6f7e8a 26%, #8f8f8f 40%, #5a5a5a 75%, #3c3c3c 100%)}
  .logo{position:absolute;top:8px;left:0;background:var(--paper);border-radius:0 20px 20px 0;display:flex;align-items:center;gap:5px;padding:4px 12px 4px 6px}
  .logo__dot{width:12px;height:12px;border-radius:50%;background:var(--logo-ink)}
  .logo__name{color:var(--logo-ink);font-weight:600;line-height:1}
  .ad__body{flex:1;display:flex;flex-direction:column;align-items:center;justify-content:space-between;text-align:center}
  .headline{color:var(--red);margin:0;font-weight:400;line-height:1.2}
  .divider{width:92%;display:flex;align-items:center;gap:6px}
  .divider::before,.divider::after{content:"";flex:1;height:1px;background:var(--rule)}
  .divider span{width:5px;height:5px;border:1px solid #555;transform:rotate(45deg)}
  .features{margin:0;text-transform:uppercase;line-height:1.5}
  .category{background:var(--red);color:#fff;font-weight:600;text-transform:uppercase;letter-spacing:.04em;padding:1px 6px}
  .products{border-radius:4px;background:linear-gradient(90deg,#f2c21a 0%,#e8b85a 20%,#d8a0c8 45%,#8a70c8 60%,#c8d8e8 75%,#e07030 100%)}
  .lineup{margin:0;text-transform:uppercase}
  .ad__footer{flex:none;background:var(--red);color:#fff;text-align:center;display:flex;flex-direction:column;justify-content:center;line-height:1.3}

  /* square */
  .ad--square{left:38px;top:237px;width:360px;height:359px}
  .ad--square .ad__photo{height:174px}
  .ad--square .logo__name{font-size:18px}
  .ad--square .ad__body{padding:5px 0 3px}
  .ad--square .headline{font-size:18px}
  .ad--square .features{font-size:9px}
  .ad--square .category{font-size:8px}
  .ad--square .products{width:58px;height:30px}
  .ad--square .lineup{font-size:8.5px}
  .ad--square .ad__footer{height:15px;font-size:8px}

  /* tall */
  .ad--tall{left:421px;top:8px;width:429px;height:588px}
  .ad--tall .ad__photo{height:259px}
  .ad--tall .logo__name{font-size:22px}
  .ad--tall .ad__body{padding:10px 0 4px}
  .ad--tall .headline{font-size:27px}
  .ad--tall .features{font-size:11.5px}
  .ad--tall .category{font-size:13px}
  .ad--tall .products{width:126px;height:76px}
  .ad--tall .lineup{font-size:11.5px}
  .ad--tall .ad__footer{height:42px;font-size:14px}

  /* column */
  .ad--column{left:873px;top:8px;width:218px;height:588px}
  .ad--column .ad__photo{height:165px}
  .ad--column .logo{top:6px;padding:2px 8px 2px 4px}
  .ad--column .logo__dot{width:8px;height:8px}
  .ad--column .logo__name{font-size:13px}
  .ad--column .ad__body{padding:16px 0 14px}
  .ad--column .headline{font-size:14px}
  .ad--column .features{font-size:7px}
  .ad--column .category{font-size:9px}
  .ad--column .products{width:160px;height:100px}
  .ad--column .lineup{font-size:9.5px;line-height:1.9}
  .ad--column .ad__footer{height:54px;font-size:9px}

  /* banner */
  .ad--banner{left:38px;top:606px;width:1114px;height:424px;flex-direction:row;background:transparent}
  .ad--banner .ad__photo{width:648px;height:100%}
  .ad--banner .logo{top:10px;padding:8px 16px 8px 8px;border-radius:0 28px 28px 0}
  .ad--banner .logo__name{font-size:28px}
  .ad--banner .panel{margin-left:7px;flex:1;background:var(--paper);display:flex;flex-direction:column}
  .ad--banner .ad__body{padding:12px 0 8px}
  .ad--banner .headline{font-size:30px}
  .ad--banner .features{font-size:15px}
  .ad--banner .category{font-size:14px}
  .ad--banner .products{width:168px;height:96px}
  .ad--banner .lineup{font-size:13.5px}
  .ad--banner .ad__footer{height:51px;font-size:15.5px}
</style>
</head>
<body>

<section class="ad ad--square">
  <div class="ad__photo" role="img" aria-label="Gloved hands holding a petri dish with a green leaf seedling, in monochrome">
    <div class="logo"><span class="logo__dot"></span><span class="logo__name">Velmira</span></div>
  </div>
  <div class="ad__body">
    <h2 class="headline">Creating Innovative Products<br>by Blending Science and Nature</h2>
    <div class="divider"><span></span></div>
    <p class="features">FDA Registered &nbsp;I&nbsp; Fast Turnaround &nbsp;I&nbsp; Low Minimums<br>Competitive Pricing &nbsp;I&nbsp; CGMP Quality Control</p>
    <div class="divider"><span></span></div>
    <span class="category">Hair Care Products</span>
    <div class="products" role="img" aria-label="Assorted colourful hair care bottles"></div>
    <p class="lineup">Shampoos &nbsp;I&nbsp; Conditioners &nbsp;I&nbsp; Pomades and Styling Products</p>
  </div>
  <footer class="ad__footer">4418 E. Corvale Avenue Building 210, Brightfield, CA 92870, &nbsp;555.210.4301 P 555.210.4302 F info@velmira.com</footer>
</section>

<section class="ad ad--tall">
  <div class="ad__photo" role="img" aria-label="Gloved hands holding a petri dish with a green leaf seedling, in monochrome">
    <div class="logo"><span class="logo__dot"></span><span class="logo__name">Velmira</span></div>
  </div>
  <div class="ad__body">
    <h2 class="headline">Creating Innovative Products<br>by Blending Science and Nature</h2>
    <div class="divider"><span></span></div>
    <p class="features">FDA Registered &nbsp;I&nbsp; Fast Turnaround &nbsp;I&nbsp; Low Minimums<br>Competitive Pricing &nbsp;I&nbsp; CGMP Quality Control</p>
    <div class="divider"><span></span></div>
    <span class="category">Hair Care Products</span>
    <div class="products" role="img" aria-label="Assorted colourful hair care bottles"></div>
    <p class="lineup">Shampoos &nbsp;I&nbsp; Conditioners &nbsp;I&nbsp; Pomades and Styling Products</p>
  </div>
  <footer class="ad__footer">4418 E. Corvale Avenue Building 210, Brightfield, CA 92870<br>555.210.4301 P 555.210.4302 F info@velmira.com</footer>
</section>

<section class="ad ad--column">
  <div class="ad__photo" role="img" aria-label="Gloved hands holding a petri dish with a green leaf seedling, in monochrome">
    <div class="logo"><span class="logo__dot"></span><span class="logo__name">Velmira</span></div>
  </div>
  <div class="ad__body">
    <h2 class="headline">Creating Innovative Products<br>by Blending Science and Nature</h2>
    <div class="divider"><span></span></div>
    <p class="features">FDA Registered &nbsp;I&nbsp; Fast Turnaround &nbsp;I&nbsp; Low Minimums<br>Competitive Pricing &nbsp;I&nbsp; CGMP Quality Control</p>
    <div class="divider"><span></span></div>
    <span class="category">Hair Care Products</span>
    <div class="products" role="img" aria-label="Assorted colourful hair care bottles"></div>
    <p class="lineup">Shampoos &nbsp;I&nbsp; Conditioners<br>I&nbsp; Pomades and Styling Products</p>
  </div>
  <footer class="ad__footer">4418 E. Corvale Avenue Building 210,<br>Brightfield, CA 92870, 555.210.4301<br>P 555.210.4302 F info@velmira.com</footer>
</section>

<section class="ad ad--banner">
  <div class="ad__photo" role="img" aria-label="Gloved hands holding a petri dish with a green leaf seedling, in monochrome">
    <div class="logo"><span class="logo__dot"></span><span class="logo__name">Velmira</span></div>
  </div>
  <div class="panel">
    <div class="ad__body">
      <h2 class="headline">Creating Innovative Products<br>by Blending Science and Nature</h2>
      <div class="divider"><span></span></div>
      <p class="features">FDA Registered &nbsp;I&nbsp; Fast Turnaround &nbsp;I&nbsp; Low Minimums<br>Competitive Pricing &nbsp;I&nbsp; CGMP Quality Control</p>
      <div class="divider"><span></span></div>
      <span class="category">Hair Care Products</span>
      <div class="products" role="img" aria-label="Assorted colourful hair care bottles"></div>
      <p class="lineup">Shampoos &nbsp;I&nbsp; Conditioners &nbsp;I&nbsp; Pomades and Styling Products</p>
    </div>
    <footer class="ad__footer">4418 E. Corvale Avenue Building 210, Brightfield, CA 92870<br>555.210.4301 P 555.210.4302 F info@velmira.com</footer>
  </div>
</section>

</body>
</html>
```